Lindqvar Foundation Letterhead

We are a newly established non profit registered in Maryland but operates in Africa, south of the sahara. We offer scholarships to deserving young adults from high school through college. Our color theme for our existing logo is purple, we want a design that is stylish, spellbinding yet a letterhead that projects seriousness. More information on www.thelindqvarfoundation.example

Target Market(s)

High school and college students in sub saharan African as well as our donors in the US

Industry/Entity Type

Non Profit

Font styles to use
Script

Requirements
Must have
• Logo at the top and if possible watermark the logo in the middle of the letterhead, contact address,
Should not have
• NA

```html
<!DOCTYPE html>
<html lang="en">
<head>
<meta charset="utf-8">
<title>Lindqvar Foundation Letterhead</title>
<link rel="stylesheet" href="https://fonts.googleapis.com/css2?family=Questrial&display=swap">
<style>
  :root {
    --backdrop: #d8d8da;
    --paper: #f7f7f7;
    --purple: #7b4fa6;
    --purple-soft: #a79bc9;
    --purple-deep: #8a62ad;
    --ink: #4a4a4a;
    --mark-faint: #ececec;
    --swoosh-grey: #dcdcdc;
  }
  * { margin: 0; padding: 0; box-sizing: border-box; }
  html, body { width: 1200px; height: 991px; overflow: hidden; }
  body { background: var(--backdrop); position: relative; }

  .letterhead {
    position: absolute; left: 312px; top: 89px;
    width: 577px; height: 813px;
    background: var(--paper);
    box-shadow: 0 2px 6px rgba(0,0,0,0.18);
    overflow: hidden;
  }

  .brand { position: absolute; left: 47px; top: 74px; display: flex; align-items: center; gap: 14px; }
  .brand-circle { width: 29px; height: 29px; border-radius: 50%; background: var(--purple-soft); }
  .brand-name { font-family: "Questrial", sans-serif; font-size: 15px; font-weight: 400; color: var(--purple); white-space: nowrap; }

  .contact { position: absolute; left: 404px; top: 48px; font-family: "Questrial", sans-serif; font-size: 8px; font-style: normal; color: var(--ink); line-height: 10.5px; }
  .contact-line { display: flex; align-items: center; gap: 5px; }
  .contact-icon { width: 8px; height: 8px; border-radius: 1.5px; background: var(--purple); display: inline-flex; }
  .contact-icon svg { width: 8px; height: 8px; }
  .contact-address { margin-top: 7px; }

  .watermark { position: absolute; left: 0; top: 255px; width: 400px; height: 560px; }
  .footer-swoosh { position: absolute; left: 0; bottom: 0; width: 577px; height: 45px; }
</style>
</head>
<body>
  <main class="letterhead">
    <header class="brand">
      <span class="brand-circle"></span>
      <span class="brand-name">Lindqvar Foundation Inc</span>
    </header>

    <address class="contact">
      <div class="contact-line"><span class="contact-icon"><svg viewBox="0 0 8 8"><path d="M2.3 1.6l1 1.2-.6.7c.4.8 1 1.4 1.8 1.8l.7-.6 1.2 1-.6.8C3.9 6.4 1.6 4.1 1.5 2.2z" fill="#fff"/></svg></span>(555) 014-2873</div>
      <div class="contact-line"><span class="contact-icon"><svg viewBox="0 0 8 8"><rect x="1.5" y="2.3" width="5" height="3.4" fill="none" stroke="#fff" stroke-width=".7"/><path d="M1.5 2.3L4 4.3l2.5-2" fill="none" stroke="#fff" stroke-width=".7"/></svg></span>info@thelindqvarfoundation.example</div>
      <div class="contact-line"><span class="contact-icon"><svg viewBox="0 0 8 8"><circle cx="4" cy="4" r="2.4" fill="none" stroke="#fff" stroke-width=".7"/><path d="M1.6 4h4.8M4 1.6c-1.2 1.4-1.2 3.4 0 4.8M4 1.6c1.2 1.4 1.2 3.4 0 4.8" fill="none" stroke="#fff" stroke-width=".5"/></svg></span>www.thelindqvarfoundation.example</div>
      <div class="contact-address">48 Harbourview Rd - Suite 200<br>Lakeside, ON Canada, A1B 2C3</div>
    </address>

    <svg class="watermark" role="img" aria-label="Faint foundation emblem watermark" viewBox="0 0 400 560">
      <defs>
        <radialGradient id="markGlow" cx="0.55" cy="0.55" r="0.55">
          <stop offset="0" stop-color="var(--mark-faint)" stop-opacity="0.9"/>
          <stop offset="1" stop-color="var(--mark-faint)" stop-opacity="0"/>
        </radialGradient>
      </defs>
      <rect width="400" height="560" fill="url(#markGlow)"/>
    </svg>

    <svg class="footer-swoosh" viewBox="0 0 577 45" preserveAspectRatio="none">
      <defs>
        <linearGradient id="swooshGrad" x1="0" x2="1">
          <stop offset="0" stop-color="var(--purple-deep)"/>
          <stop offset="0.6" stop-color="var(--purple-soft)"/>
          <stop offset="1" stop-color="var(--purple-deep)"/>
        </linearGradient>
      </defs>
      <path d="M0 20 C80 30 150 25 250 12 C350 0 470 4 577 27 L577 45 L0 45Z" fill="var(--purple-deep)" opacity="0.75"/>
      <path d="M120 45 C250 20 400 4 577 30 L577 45Z" fill="var(--swoosh-grey)"/>
      <path d="M180 45 C300 25 430 12 577 34 L577 45Z" fill="url(#swooshGrad)"/>
    </svg>
  </main>
</body>
</html>
```